Copper lark buildworks

Copper lark buildworks is a small construction company.
Who is a licenced builder, Carpenter, joiner,
working on heritage ,new build, speacial projects and sometimes furniture

Industry/Entity Type

Construction

```html
<!DOCTYPE html>
<html lang="en">
<head>
<meta charset="utf-8">
<title>Copper lark buildworks – business card</title>
<link href="https://fonts.googleapis.com/css2?family=Montserrat:wght@400;500;700;800&display=swap" rel="stylesheet">
<style>
  :root {
    --page: #e9e9e6;
    --card-white: #f4f4f2;
    --card-black: #050505;
    --brand-green: #3f8a12;
    --bright-green: #4caf1a;
    --ink: #222222;
    --rule: #333333;
    --light: #ffffff;
  }
  * { margin: 0; padding: 0; box-sizing: border-box; }
  html, body {
    width: 1200px; height: 1000px; overflow: hidden;
    background: var(--page);
    font-family: "Montserrat", Arial, sans-serif;
  }
  .business-card {
    position: absolute; left: 150px; top: 243px;
    width: 900px; height: 514px;
    border-radius: 26px; overflow: hidden;
    background: var(--card-white);
    box-shadow: 0 10px 30px rgba(0,0,0,.18);
  }
  .card-shapes { position: absolute; inset: 0; }
  .brand-name {
    position: absolute; right: 44px; top: 32px;
    text-align: right;
    font-weight: 800; font-size: 44px; line-height: 46px;
    letter-spacing: -0.5px; color: var(--brand-green);
    text-transform: uppercase;
  }
  .tagline {
    position: absolute; right: 44px; top: 138px; width: 360px;
    padding: 7px 0 8px;
    border-top: 1.5px solid var(--rule);
    border-bottom: 1.5px solid var(--rule);
    text-align: right;
    font-size: 17px; line-height: 21px; color: var(--ink);
  }
  .tagline strong { color: var(--brand-green); font-weight: 700; }
  .holder-marker {
    position: absolute; left: 0; top: 364px;
    width: 40px; height: 44px; background: var(--bright-green);
  }
  .holder { position: absolute; left: 58px; top: 350px; }
  .holder-name {
    font-weight: 700; font-size: 27px; line-height: 30px;
    color: var(--bright-green);
  }
  .holder-role { font-size: 18px; line-height: 22px; color: var(--light); }
  .address {
    position: absolute; right: 44px; top: 410px;
    font-size: 19px; color: var(--light);
  }
  .contact-line {
    position: absolute; left: 58px; right: 44px; top: 452px;
    display: flex; justify-content: flex-end; align-items: center; gap: 10px;
    font-size: 19px; color: var(--light); white-space: nowrap;
  }
  .contact-item { display: inline-flex; align-items: center; gap: 7px; }
  .contact-item svg { width: 20px; height: 20px; flex: none; }
  .web-name { color: var(--bright-green); font-weight: 500; }
</style>
</head>
<body>
  <div class="business-card">
    <svg class="card-shapes" viewBox="0 0 900 514" preserveAspectRatio="none" aria-hidden="true">
      <path d="M0,262 Q330,372 900,222 L900,514 L0,514 Z" fill="var(--bright-green)"/>
      <path d="M0,262 Q330,362 900,262 L900,514 L0,514 Z" fill="var(--card-black)"/>
    </svg>

    <div class="brand-name">Copper lark<br>buildworks</div>

    <p class="tagline">working on <strong>heritage, new build,</strong><br><strong>speacial projects, and furniture</strong></p>

    <div class="holder-marker"></div>
    <div class="holder">
      <p class="holder-name">Marcus Hale</p>
      <p class="holder-role">Licenced Builder &amp; Carpenter</p>
    </div>

    <p class="address">12 Harbour Lane Singapore 40213</p>

    <div class="contact-line">
      <span class="contact-item">
        <svg viewBox="0 0 20 20"><path d="M3 7c0-3 3-4 7-4s7 1 7 4l-3 1-1-2H7L6 8 3 7Z M5 10h10l2 6H3l2-6Z M8 12h4v2H8Z" fill="var(--bright-green)"/></svg>
        <span>0400123987</span>
      </span>
      <span>|</span>
      <span class="contact-item">
        <svg viewBox="0 0 20 20"><circle cx="10" cy="10" r="9" fill="var(--bright-green)"/><rect x="5" y="6.5" width="10" height="7" fill="none" stroke="var(--card-black)" stroke-width="1.4"/><path d="M5 6.5l5 4 5-4" fill="none" stroke="var(--card-black)" stroke-width="1.4"/></svg>
        <span>marcus@copperlark.com</span>
      </span>
      <span>|</span>
      <span class="contact-item">
        <svg viewBox="0 0 20 20"><circle cx="10" cy="10" r="9" fill="var(--bright-green)"/><g fill="none" stroke="var(--card-black)" stroke-width="1.2"><circle cx="10" cy="10" r="5.5"/><ellipse cx="10" cy="10" rx="2.4" ry="5.5"/><path d="M4.5 10h11"/></g></svg>
        <span>www.<span class="web-name">copperlark</span>.com</span>
      </span>
    </div>
  </div>
</body>
</html>
```